Small Business Consulting Firm Needs Letterhead

We need a letterhead for our company "Brightpath Plus". Our company does outbound calling and mailing to business owner's companies who have taken high interest loans. These loans tend to put these businesses in a big financial bind short term, and we help them find better financial options. We would like the design to match our colors of our logo. Headers and footers would look nice, but we are open. We would want it to include our address, website, phone, and email info. Our address - 2000 E. Lamar Blvd. Suite 600Website - www.safeguardtoday.comEmail - info@safeguardtoday.comPhone - 855-726-1938
Industry/Entity Type
Financial Planning
Look and feel
Each slider illustrates characteristics of the customer's brand and the style your logo design should communicate.

```html
<!DOCTYPE html>
<html lang="en">
<head>
<meta charset="utf-8">
<title>Brightpath Plus Letterhead</title>
<link href="https://fonts.googleapis.com/css2?family=Open+Sans:wght@400;600&family=Lato:wght@400;700&display=swap" rel="stylesheet">
<style>
  :root {
    --green: #6cb33f;
    --green-dark: #4f8f2c;
    --blue: #1f6fb2;
    --blue-dark: #135a94;
    --blue-light: #1f8ad6;
    --ink: #3c3c3c;
    --ink-strong: #222;
    --rule: #b5b5b5;
    --paper: #ffffff;
  }
  * { margin: 0; padding: 0; box-sizing: border-box; }
  html, body { width: 1040px; height: 1200px; overflow: hidden; background: var(--paper); }
  .letterhead {
    position: relative;
    width: 1040px;
    height: 1200px;
    background: var(--paper);
    font-family: "Open Sans", sans-serif;
    color: var(--ink);
  }
  .decor { position: absolute; inset: 0; width: 1040px; height: 1200px; }
  .brand {
    position: absolute;
    top: 92px;
    left: 0;
    width: 1040px;
    display: flex;
    justify-content: center;
    align-items: center;
    gap: 12px;
  }
  .brand-square { width: 22px; height: 22px; background: var(--green); }
  .brand-name {
    font-size: 22px;
    font-weight: 400;
    letter-spacing: 2px;
    text-transform: uppercase;
    color: #333;
  }
  .letter {
    position: absolute;
    left: 97px;
    width: 840px;
    font-size: 15px;
    line-height: 27px;
  }
  .issue-date { top: 212px; }
  .recipient { top: 252px; line-height: 18px; }
  .salutation { top: 353px; }
  .body-copy { top: 407px; text-align: justify; hyphens: auto; }
  .body-copy p + p { margin-top: 27px; }
  .closing { top: 811px; }
  .signer { top: 888px; }
  .signer-name { font-size: 19px; font-weight: 600; color: var(--ink-strong); line-height: 28px; }
  .signer-title { font-size: 15px; line-height: 24px; }
  .footer-address {
    position: absolute;
    top: 1118px;
    left: 0;
    width: 1040px;
    text-align: center;
    font-family: "Lato", sans-serif;
    font-size: 18px;
    color: #111;
  }
  .footer-contact {
    position: absolute;
    top: 1150px;
    left: 0;
    width: 1040px;
    text-align: center;
    font-family: "Lato", sans-serif;
    font-size: 18px;
    color: #111;
  }
  .footer-contact .label { color: var(--blue-light); font-weight: 700; }
  .footer-contact .web { color: var(--blue-light); }
</style>
</head>
<body>
<main class="letterhead">
  <svg class="decor" viewBox="0 0 1040 1200" aria-hidden="true">
    <!-- header band -->
    <polygon points="0,0 842,0 868,24 0,24" fill="var(--green)"/>
    <polygon points="875,0 1040,0 1040,183 1005,148 1005,28 895,28" fill="var(--green-dark)"/>
    <polygon points="1005,28 1040,0 1040,183 1005,148" fill="var(--green)"/>
    <!-- footer band -->
    <line x1="103" y1="1146" x2="935" y2="1146" stroke="var(--rule)" stroke-width="1.5"/>
    <polygon points="92,1176 1040,1176 1040,1200 116,1200" fill="var(--blue)"/>
    <polygon points="0,1118 32,1150 32,1176 80,1176 104,1200 0,1200" fill="var(--blue-dark)"/>
    <polygon points="32,1176 80,1176 104,1200 10,1200" fill="var(--blue-light)"/>
  </svg>

  <header class="brand">
    <span class="brand-square"></span>
    <span class="brand-name">Brightpath Plus</span>
  </header>

  <p class="letter issue-date">Issuing Date: May 5, 2018</p>
  <p class="letter recipient">Name Of Employee Mr. XYZABC<br>Address of Employee<br>Address Line 2 etc..</p>
  <p class="letter salutation">Dear Mr.XYZABC</p>

  <section class="letter body-copy">
    <p>Lorem Ipsum has been the industry's standard dummy text ever since the 1500s, when an unknown printer took a galley of type and scrambled it to make a type specimen book. It has survived not only five centuries, but also the leap into electronic typesetting, remaining essentially unchanged. It was popularised in the 1960s with the release of Typeline sheets containing Lorem Ipsum passages, and more recently with desktop publishing software like Quillset Composer including versions of Lorem Ipsum.</p>
    <p>Lorem Ipsum is simply dummy text of the printing and typesetting industry. Lorem Ipsum has been the industry's standard dummy text ever since the 1500s, when an unknown printer took a galley of type and scrambled it to make a type specimen book.</p>
    <p>It has survived not only five centuries, but also the leap into electronic typesetting, remaining essentially unchanged. It was popularised in the 1960s with the release of Typeline sheets containing Lorem IpsumIpsum passages.</p>
  </section>

  <p class="letter closing">Yours Sincerely</p>
  <div class="letter signer">
    <p class="signer-name">Dorian Kessler</p>
    <p class="signer-title">Managing Director</p>
  </div>

  <footer>
    <p class="footer-address">4170 W. Corwin Ave. Suite 310</p>
    <p class="footer-contact"><span class="label">P:</span> 855-726-1938 &nbsp;| <span class="label">E:</span> info@brightpathplus.com | <span class="web">www.brightpathplus.com</span></p>
  </footer>
</main>
</body>
</html>
```